project - Misto Den

Dear designers, I'm Looking for an appealing new business card design to represent us for our new e-cigarette store: The MistO Den. Knowledgeable and friendly staff we aim for superior customer service with a positive atmosphere. Classic feel with modern touch is what we are aiming for . Lime green font and grey back round is the original color scheme but we are flexible and open to suggestions. I added some doodles to show you where my mind is at. address: 4827 203 St SW Edmonton, AB (inside the grand swap bazaar)web: themistoden.com email: info@themistoden.com phone : 555.214.6093 Thanks and am looking forward to seeing your creative , fresh and innovative designs.
Good luck everybody!
Gordon
Updates
lime green and charcoal grey please. thanks
Industry/Entity Type
Business
Logo Text
The MistO Den
Look and feel
Each slider illustrates characteristics of the customer's brand and the style your logo design should communicate.

```html
<!DOCTYPE html>
<html lang="en">
<head>
<meta charset="utf-8">
<title>Misto Den – Business Card</title>
<link rel="stylesheet" href="https://fonts.googleapis.com/css2?family=Cinzel:wght@400&family=Electrolize&display=swap">
<style>
  :root {
    --stage: #2b2e2d;
    --charcoal: #5f6261;
    --charcoal-dark: #4a4d4c;
    --lime: #8cc63f;
    --lime-light: #a6d352;
    --paper: #ffffff;
    --ink: #4d4f4f;
    --white-text: #ffffff;
  }
  * { box-sizing: border-box; margin: 0; padding: 0; }
  html, body { width: 1200px; height: 898px; overflow: hidden; }
  body {
    background: var(--stage);
    display: flex;
    flex-direction: column;
    align-items: center;
    justify-content: center;
    gap: 44px;
  }
  .card {
    width: 660px;
    height: 377px;
    position: relative;
    overflow: hidden;
    box-shadow: 0 14px 30px rgba(0,0,0,.45);
  }
  .wordmark {
    font-family: "Cinzel", "Trajan Pro", serif;
    font-weight: 400;
    letter-spacing: 1px;
    white-space: nowrap;
  }

  /* Back side */
  .card-back {
    background: linear-gradient(135deg, var(--charcoal) 0%, var(--charcoal-dark) 100%);
    display: flex;
    align-items: center;
    justify-content: center;
  }
  .card-back .wordmark {
    font-size: 64px;
    color: var(--lime);
  }

  /* Front side */
  .card-front { background: var(--paper); display: flex; }
  .edge-band {
    position: absolute; left: 0; top: 0; bottom: 0; width: 14px;
    background: var(--lime);
  }
  .edge-accent {
    position: absolute; left: 14px; top: 150px; width: 14px; height: 227px;
    background: var(--charcoal);
    clip-path: polygon(0 0, 100% 14%, 100% 100%, 0 100%);
  }
  .brand-panel {
    width: 57%;
    position: relative;
  }
  .brand-panel .wordmark {
    position: absolute;
    left: 78px;
    top: 210px;
    font-size: 40px;
    color: var(--ink);
  }
  .contact-panel {
    width: 43%;
    background: linear-gradient(160deg, var(--lime) 0%, var(--lime-light) 60%, var(--lime) 100%);
    color: var(--white-text);
    font-family: "Electrolize", "Arial", sans-serif;
    text-align: right;
    padding: 30px 26px 0 10px;
  }
  .holder-name { font-size: 17px; letter-spacing: 1.5px; }
  .holder-title { font-size: 12px; letter-spacing: 1.5px; margin-top: 3px; }
  .address { font-size: 13px; line-height: 1.45; margin-top: 30px; letter-spacing: .5px; }
  .lines { list-style: none; margin-top: 24px; font-size: 12px; letter-spacing: .5px; }
  .lines li {
    display: flex; justify-content: flex-end; align-items: center;
    gap: 7px; line-height: 1.95;
  }
  .lines svg { width: 12px; height: 12px; fill: none; stroke: var(--white-text); stroke-width: 1.6; }
  .lines .plain { padding-right: 19px; }
</style>
</head>
<body>
  <section class="card card-back" aria-label="Card back">
    <span class="wordmark">MISTO DEN</span>
  </section>

  <section class="card card-front" aria-label="Card front">
    <span class="edge-band"></span>
    <span class="edge-accent"></span>
    <div class="brand-panel">
      <span class="wordmark">MISTO DEN</span>
    </div>
    <div class="contact-panel">
      <p class="holder-name">ALAN REYES</p>
      <p class="holder-title">GENERAL MANAGER</p>
      <p class="address">4827 203 St SW,<br>Edmonton, AB</p>
      <ul class="lines">
        <li>555.214.6093
          <svg viewBox="0 0 12 12"><path d="M2 1.5l2 0 1 2.5-1.2 1a6 6 0 0 0 3.2 3.2l1-1.2 2.5 1v2a1 1 0 0 1-1 1A9 9 0 0 1 1 2.5a1 1 0 0 1 1-1z"/></svg>
        </li>
        <li>555.214.6094
          <svg viewBox="0 0 12 12"><rect x="3" y="1" width="6" height="10" rx="1"/><path d="M5.2 9.2h1.6"/></svg>
        </li>
        <li>555.214.6095
          <svg viewBox="0 0 12 12"><rect x="1.5" y="5" width="9" height="5.5" rx=".8"/><path d="M3.5 5V1.5h5V5"/></svg>
        </li>
        <li>info@themistoden.com
          <svg viewBox="0 0 12 12"><rect x="1" y="2.5" width="10" height="7" rx=".8"/><path d="M1 3l5 3.8L11 3"/></svg>
        </li>
        <li>www.themistoden.com
          <svg viewBox="0 0 12 12"><circle cx="6" cy="6" r="5"/><ellipse cx="6" cy="6" rx="2.2" ry="5"/><path d="M1 6h10"/></svg>
        </li>
      </ul>
    </div>
  </section>
</body>
</html>
```